Verodex business card

Business card for sustainable investment company called "Verodex". Verodex is an exchange platform selling carbon credits between buyers and sellers. Carbon Credits are an environmental commodity for reducing global carbon emissions.

the card should obviously have our logo and the theme should be sustainability/environment mixed with a trading platform.

Contact Information for Business Card

Logo, Name, Title, Phone, Email

Colors
0054AA
0677BA
7BADD7
CADEEF
E8F1F8
0094D4
00A9DD
6FCCEA
C7EBF8
E9F6FB
00AB8E
00BBA5
67D7C9
C6EFE9
E9F9F6
59FF00
82FF00
B8FF75
E3FFCB
F4FFEA

```html
<!DOCTYPE html>
<html lang="en">
<head>
<meta charset="UTF-8">
<title>Verodex Business Card</title>
<link href="https://fonts.googleapis.com/css2?family=Montserrat:wght@500;600;700&display=swap" rel="stylesheet">
<style>
  :root {
    --page-bg: #1b1c1e;
    --card-dark: #08090b;
    --card-light: #2b2c2e;
    --accent: #4a9fd8;
    --accent-deep: #3b7fd0;
    --ink: #ffffff;
    --ink-soft: #e6e8ea;
  }
  * { margin: 0; padding: 0; box-sizing: border-box; }
  html, body {
    width: 1200px;
    height: 900px;
    overflow: hidden;
    background: var(--page-bg);
    font-family: "Montserrat", sans-serif;
    color: var(--ink);
  }
  .sheet {
    width: 1200px;
    height: 900px;
    display: flex;
    flex-direction: column;
    align-items: center;
    justify-content: center;
    gap: 40px;
  }
  .card {
    position: relative;
    width: 760px;
    height: 400px;
    background: linear-gradient(115deg, var(--card-dark) 0%, #111214 45%, var(--card-light) 100%);
    box-shadow: 0 14px 34px rgba(0, 0, 0, 0.55);
  }

  /* Brand lockup */
  .brand {
    display: flex;
    align-items: center;
    gap: 18px;
  }
  .brand-dot {
    border-radius: 50%;
    background: var(--accent);
    flex: none;
  }
  .brand-name {
    font-weight: 600;
    color: var(--ink);
    letter-spacing: 0.02em;
    text-transform: uppercase;
    line-height: 1;
  }

  /* Front */
  .card-front {
    display: flex;
    align-items: center;
    justify-content: center;
  }
  .card-front .brand-dot { width: 70px; height: 70px; }
  .card-front .brand-name { font-size: 68px; }

  /* Back */
  .card-back .brand {
    position: absolute;
    left: 48px;
    top: 170px;
    gap: 14px;
  }
  .card-back .brand-dot { width: 48px; height: 48px; }
  .card-back .brand-name { font-size: 40px; }

  .divider {
    position: absolute;
    left: 372px;
    top: 95px;
    width: 2px;
    height: 215px;
    background: var(--accent);
  }
  .details {
    position: absolute;
    left: 400px;
    top: 92px;
    right: 24px;
  }
  .person-name {
    font-size: 32px;
    font-weight: 700;
    color: var(--accent);
    letter-spacing: 0.06em;
    text-transform: uppercase;
    line-height: 1;
  }
  .person-title {
    font-size: 17px;
    font-weight: 500;
    letter-spacing: 0.06em;
    text-transform: uppercase;
    margin-top: 4px;
    color: var(--ink-soft);
  }
  .address {
    font-size: 16px;
    font-weight: 500;
    line-height: 1.3;
    margin-top: 20px;
    font-style: normal;
    color: var(--ink-soft);
    letter-spacing: 0.02em;
  }
  .contact-list {
    list-style: none;
    margin-top: 18px;
  }
  .contact-item {
    display: flex;
    align-items: center;
    gap: 12px;
    font-size: 18px;
    font-weight: 500;
    letter-spacing: 0.03em;
    line-height: 1.55;
    color: var(--ink-soft);
  }
  .contact-icon {
    width: 16px;
    height: 16px;
    flex: none;
  }
</style>
</head>
<body>
<main class="sheet">

  <section class="card card-front" aria-label="Card front">
    <div class="brand">
      <span class="brand-dot"></span>
      <span class="brand-name">Verodex</span>
    </div>
  </section>

  <section class="card card-back" aria-label="Card back">
    <div class="brand">
      <span class="brand-dot"></span>
      <span class="brand-name">Verodex</span>
    </div>

    <div class="divider"></div>

    <div class="details">
      <h1 class="person-name">Dana Whitfield</h1>
      <p class="person-title">Manager</p>
      <address class="address">2250 Harbor Crest Rd. Suite 14<br>Lakeview, OR 97630</address>
      <ul class="contact-list">
        <li class="contact-item">
          <svg class="contact-icon" viewBox="0 0 24 24" aria-hidden="true">
            <path fill="var(--accent)" d="M6.6 10.8a15.1 15.1 0 0 0 6.6 6.6l2.2-2.2a1 1 0 0 1 1-.25 11.4 11.4 0 0 0 3.6.57 1 1 0 0 1 1 1V20a1 1 0 0 1-1 1A17 17 0 0 1 3 4a1 1 0 0 1 1-1h3.5a1 1 0 0 1 1 1c0 1.25.2 2.46.57 3.6a1 1 0 0 1-.25 1z"/>
          </svg>
          555-018-2746
        </li>
        <li class="contact-item">
          <svg class="contact-icon" viewBox="0 0 24 24" aria-hidden="true">
            <path fill="var(--accent)" d="M2 5h20v14H2z"/>
            <path fill="none" stroke="#111214" stroke-width="2" d="M2 5l10 8 10-8"/>
          </svg>
          hello@verodex.com
        </li>
        <li class="contact-item">
          <svg class="contact-icon" viewBox="0 0 24 24" aria-hidden="true">
            <g fill="none" stroke="var(--accent)" stroke-width="2">
              <circle cx="12" cy="12" r="10"/>
              <ellipse cx="12" cy="12" rx="4.5" ry="10"/>
              <path d="M2 12h20M4 7h16M4 17h16"/>
            </g>
          </svg>
          www.verodex.com
        </li>
      </ul>
    </div>
  </section>

</main>
</body>
</html>
```